Q&J RESTORATION

I want a brochure similiar to the example i've attached.
My company name is Q&J Restoration. The website is: Q-J-Restoration.example.
The phone number is 919.555.0147.

I don't like the "yellow" being the main color of the example so I'm open to suggestions. I want something CLEAN & Simple, like our logo . This will be a bi fold brochure

```html
<!DOCTYPE html>
<html lang="en">
<head>
<meta charset="utf-8">
<title>Q&amp;J Restoration – Bi-fold Brochure</title>
<link rel="stylesheet" href="https://fonts.googleapis.com/css2?family=Raleway:wght@300;400;500;600;700&display=swap">
<style>
  :root{
    --sky:#16b5ec;
    --sky-deep:#0b8dc6;
    --ink:#1d2530;
    --header:rgba(34,44,56,.88);
    --band:rgba(14,16,20,.78);
    --contact:rgba(22,42,66,.9);
    --white:#ffffff;
    --paper:#f4f5f6;
    --kitchen-a:#e8e1d2;
    --kitchen-b:#b98659;
    --kitchen-c:#f3efe6;
  }
  *{box-sizing:border-box;margin:0;padding:0}
  html,body{width:1200px;height:838px;overflow:hidden}
  body{background:var(--paper);position:relative;font-family:"Raleway",sans-serif;color:var(--white)}

  /* placement of the six panels */
  .sheet{position:absolute;top:69.5px;font-size:10px}
  .sheet--p1{left:36.6px}
  .sheet--p2{left:332.4px}
  .sheet--p3{left:630.8px}
  .sheet--p4{left:926px}
  .spread{position:absolute;top:453.6px;display:flex;font-size:11.15px}
  .spread--outside{left:36.6px}
  .spread--inside{left:630.8px}

  .page{position:relative;width:24em;height:31.1em;overflow:hidden}
  .page__art{position:absolute;inset:0;width:100%;height:100%}

  /* ---------- cover ---------- */
  .cover__photo{position:absolute;inset:0;background:linear-gradient(160deg,#3d4d5c 0%,#27323d 45%,#1b3d52 80%,#16506b 100%)}
  .cover__logo{position:absolute;top:44%;left:10%;right:0;text-align:center;font-weight:300;font-size:1.75em;letter-spacing:.04em;line-height:1}
  .cover__band{position:absolute;top:61.2%;height:6.8%;left:10.4%;right:0;background:var(--band);display:flex;align-items:center;justify-content:center}
  .cover__tagline{font-size:.86em;font-weight:400;letter-spacing:.3em}
  .cover__url{position:absolute;top:71.4%;left:10.4%;right:0;text-align:center;font-size:.82em;font-weight:300}

  /* ---------- inside ---------- */
  .inside__photo{position:absolute;left:0;right:0;top:0;height:68%;background:linear-gradient(120deg,var(--kitchen-c) 0%,var(--kitchen-a) 40%,#d3b48c 70%,var(--kitchen-b) 100%)}
  .inside__header{position:absolute;left:0;right:0;top:0;height:16.6%;background:var(--header);padding:1.2em 1.4em 0}
  .inside__title{font-size:1.05em;font-weight:600;line-height:1.2}
  .inside__subtitle{font-size:.7em;font-weight:600;margin-top:.55em}
  .inside__panel{position:absolute;left:0;right:0;top:68%;bottom:0;background:var(--sky-deep);display:grid;grid-template-columns:1fr 1fr;padding:1.1em 0 1.2em 1.4em}
  .step{padding-right:.6em}
  .step + .step{border-left:1px solid rgba(255,255,255,.75);padding-left:1.1em}
  .step__title{font-size:.72em;font-weight:600;margin-bottom:.45em;white-space:nowrap}
  .step__text{font-size:.58em;font-weight:300;line-height:1.62}

  /* ---------- back ---------- */
  .back{background:var(--sky)}
  .back__blueprint{position:absolute;inset:0;background:linear-gradient(135deg,#1cbdf2 0%,#12aee6 55%,#0fa6df 100%)}
  .back__title{position:absolute;top:6.5%;left:0;right:0;text-align:center;color:var(--ink);font-size:1.3em;font-weight:600;line-height:1.15}
  .back__title span{font-weight:400}
  .back__logo{position:absolute;top:23%;left:0;right:0;text-align:center;color:var(--ink);font-weight:300;font-size:1.35em;letter-spacing:.04em;line-height:1}
  .review{position:absolute;left:1.8em;right:1.8em;text-align:center;color:var(--ink)}
  .review--1{top:37.8%}
  .review--2{top:52.8%}
  .review--3{top:72.8%}
  .review__name{font-size:.74em;font-weight:600;margin-bottom:.3em}
  .review__text{font-size:.57em;font-weight:300;line-height:1.55}
  .back__contact{position:absolute;left:0;right:0;top:88%;height:7.3%;background:var(--contact);display:flex;align-items:center;justify-content:center;gap:1.1em;font-size:.66em;font-weight:600;white-space:nowrap}
  .contact__item{display:flex;align-items:center;gap:.5em}
  .contact__icon{width:.9em;height:.9em;fill:var(--white)}
  .contact__sep{opacity:.8;padding:0 .25em}
</style>
</head>
<body>

<!-- single panels -->
<div class="sheet sheet--p1">
  <section class="page cover">
    <div class="cover__photo" role="img" aria-label="Photo of a flooded living room interior"></div>
    <svg class="page__art" viewBox="0 0 240 311" preserveAspectRatio="none" aria-hidden="true">
      <path fill="#16b5ec" fill-opacity=".86" fill-rule="evenodd" d="M0 0H240V311H0Z M221 155.5m-197 0a197 197 0 1 0 394 0a197 197 0 1 0 -394 0"/>
      <circle cx="221" cy="155.5" r="197" fill="#2c323d" fill-opacity=".72"/>
    </svg>
    <div class="cover__logo">Q&amp;J Restoration</div>
    <div class="cover__band"><span class="cover__tagline">Insurance Claim Specialist</span></div>
    <div class="cover__url">www.Q-J-Restoration.example</div>
  </section>
</div>

<div class="sheet sheet--p2">
  <section class="page inside">
    <div class="inside__photo" role="img" aria-label="Hands framing a kitchen half sketched, half finished"></div>
    <svg class="page__art" viewBox="0 0 240 311" preserveAspectRatio="none" aria-hidden="true">
      <path fill="#16b5ec" fill-rule="evenodd" d="M0 52H240V212H0Z M260 125m-226 0a226 226 0 1 0 452 0a226 226 0 1 0 -452 0"/>
    </svg>
    <header class="inside__header">
      <h2 class="inside__title">Restoration or Renovation?</h2>
      <p class="inside__subtitle">What happens after the cleanup?</p>
    </header>
    <div class="inside__panel">
      <div class="step"><h3 class="step__title">1. Adjuster's Inspection</h3><p class="step__text">Feel Confident. Be sure you received a fair and accurate assessment &amp; repair of all damages with our team's use of industry leading Estimating Systems and On-Site Review.</p></div>
      <div class="step"><h3 class="step__title">2. Timely Settlement</h3><p class="step__text">Don't wait. Minimize the hassle of long processing times from Estimate to Settlement when you team up with an Insurance Claim Specialist.</p></div>
    </div>
  </section>
</div>

<div class="sheet sheet--p3">
  <section class="page inside">
    <div class="inside__photo" role="img" aria-label="Hands framing a finished kitchen with granite counters"></div>
    <header class="inside__header">
      <h2 class="inside__title">Here For You, Every Step Of The Way</h2>
      <p class="inside__subtitle">www.Q-J-Restoration.example</p>
    </header>
    <div class="inside__panel">
      <div class="step"><h3 class="step__title">3. Under One Roof</h3><p class="step__text">Don't Worry. You won't need to arrange meetings with multiple contractors; we'll take care of everything from demo to final cleanup.</p></div>
      <div class="step"><h3 class="step__title">4. Superior Craftsmanship</h3><p class="step__text">Don't settle for satisfactory. Our team is committed to the highest standards of excellence every step of the way. Trust us when we say that we'll make you smile.</p></div>
    </div>
  </section>
</div>

<div class="sheet sheet--p4">
  <section class="page back">
    <div class="back__blueprint" role="img" aria-label="Faint blueprint drawings in blue tones"></div>
    <h2 class="back__title">Specializing <span>in</span><br>Insurance Claims</h2>
    <div class="back__logo">Q&amp;J Restoration</div>
    <div class="review review--1"><p class="review__name">Owen T</p><p class="review__text">Grant was so great to work with. He made dealing with my insurance company simple and easy. Highly recommend.</p></div>
    <div class="review review--2"><p class="review__name">Lena P</p><p class="review__text">Q&amp;J Restoration was a pleasure to work with. They worked with my insurance company on my behalf to ensure I received a fair settlement and that my home was restored properly after unfortunate water damage.</p></div>
    <div class="review review--3"><p class="review__name">Nora K</p><p class="review__text">Very professional, responsive, and efficient. They repaired my home in just a few weeks</p></div>
    <div class="back__contact">
      <span class="contact__item"><svg class="contact__icon" viewBox="0 0 16 16" aria-hidden="true"><path d="M1 3h14v10H1z M2 4l6 5 6-5" fill="#fff" stroke="#162a42" stroke-width="1.2"/></svg>www.Q-J-Restoration.example</span>
      <span class="contact__item"><svg class="contact__icon" viewBox="0 0 16 16" aria-hidden="true"><path d="M4 1l3 3-2 2c1 2 3 4 5 5l2-2 3 3-2 3C7 14 2 9 1 3z"/></svg>919.555.0147<span class="contact__sep">|</span>919.555.0183</span>
    </div>
  </section>
</div>

<!-- outside spread: back + cover -->
<div class="spread spread--outside">
  <section class="page back">
    <div class="back__blueprint" role="img" aria-label="Faint blueprint drawings in blue tones"></div>
    <h2 class="back__title">Specializing <span>in</span><br>Insurance Claims</h2>
    <div class="back__logo">Q&amp;J Restoration</div>
    <div class="review review--1"><p class="review__name">Owen T</p><p class="review__text">Grant was so great to work with. He made dealing with my insurance company simple and easy. Highly recommend.</p></div>
    <div class="review review--2"><p class="review__name">Lena P</p><p class="review__text">Q&amp;J Restoration was a pleasure to work with. They worked with my insurance company on my behalf to ensure I received a fair settlement and that my home was restored properly after unfortunate water damage.</p></div>
    <div class="review review--3"><p class="review__name">Nora K</p><p class="review__text">Very professional, responsive, and efficient. They repaired my home in just a few weeks</p></div>
    <div class="back__contact">
      <span class="contact__item"><svg class="contact__icon" viewBox="0 0 16 16" aria-hidden="true"><path d="M1 3h14v10H1z M2 4l6 5 6-5" fill="#fff" stroke="#162a42" stroke-width="1.2"/></svg>www.Q-J-Restoration.example</span>
      <span class="contact__item"><svg class="contact__icon" viewBox="0 0 16 16" aria-hidden="true"><path d="M4 1l3 3-2 2c1 2 3 4 5 5l2-2 3 3-2 3C7 14 2 9 1 3z"/></svg>919.555.0147<span class="contact__sep">|</span>919.555.0183</span>
    </div>
  </section>
  <section class="page cover">
    <div class="cover__photo" role="img" aria-label="Photo of a flooded living room interior"></div>
    <svg class="page__art" viewBox="0 0 240 311" preserveAspectRatio="none" aria-hidden="true">
      <path fill="#16b5ec" fill-opacity=".86" fill-rule="evenodd" d="M0 0H240V311H0Z M221 155.5m-197 0a197 197 0 1 0 394 0a197 197 0 1 0 -394 0"/>
      <circle cx="221" cy="155.5" r="197" fill="#2c323d" fill-opacity=".72"/>
    </svg>
    <div class="cover__logo">Q&amp;J Restoration</div>
    <div class="cover__band"><span class="cover__tagline">Insurance Claim Specialist</span></div>
    <div class="cover__url">www.Q-J-Restoration.example</div>
  </section>
</div>

<!-- inside spread -->
<div class="spread spread--inside">
  <section class="page inside">
    <div class="inside__photo" role="img" aria-label="Hands framing a kitchen half sketched, half finished"></div>
    <svg class="page__art" viewBox="0 0 240 311" preserveAspectRatio="none" aria-hidden="true">
      <path fill="#16b5ec" fill-rule="evenodd" d="M0 52H240V212H0Z M260 125m-226 0a226 226 0 1 0 452 0a226 226 0 1 0 -452 0"/>
    </svg>
    <header class="inside__header">
      <h2 class="inside__title">Restoration or Renovation?</h2>
      <p class="inside__subtitle">What happens after the cleanup?</p>
    </header>
    <div class="inside__panel">
      <div class="step"><h3 class="step__title">1. Adjuster's Inspection</h3><p class="step__text">Feel Confident. Be sure you received a fair and accurate assessment &amp; repair of all damages with our team's use of industry leading Estimating Systems and On-Site Review.</p></div>
      <div class="step"><h3 class="step__title">2. Timely Settlement</h3><p class="step__text">Don't wait. Minimize the hassle of long processing times from Estimate to Settlement when you team up with an Insurance Claim Specialist.</p></div>
    </div>
  </section>
  <section class="page inside">
    <div class="inside__photo" role="img" aria-label="Hands framing a finished kitchen with granite counters"></div>
    <header class="inside__header">
      <h2 class="inside__title">Here For You, Every Step Of The Way</h2>
      <p class="inside__subtitle">www.Q-J-Restoration.example</p>
    </header>
    <div class="inside__panel">
      <div class="step"><h3 class="step__title">3. Under One Roof</h3><p class="step__text">Don't Worry. You won't need to arrange meetings with multiple contractors; we'll take care of everything from demo to final cleanup.</p></div>
      <div class="step"><h3 class="step__title">4. Superior Craftsmanship</h3><p class="step__text">Don't settle for satisfactory. Our team is committed to the highest standards of excellence every step of the way. Trust us when we say that we'll make you smile.</p></div>
    </div>
  </section>
</div>

</body>
</html>
```